TA BRAMLEY BUSINESS CARD DESIGN PROJECT

We need to utilize our logo that was expertly created on PixelHarbor and now need to match this with a business card design.

```html
<!DOCTYPE html>
<html lang="en">
<head>
<meta charset="utf-8">
<title>TA BRAMLEY Business Card</title>
<link rel="stylesheet" href="https://fonts.googleapis.com/css2?family=Montserrat:wght@400;500;700&display=swap">
<style>
  :root {
    --backdrop: #d9d9d7;
    --card-white: #ffffff;
    --card-black: #161616;
    --brand-blue: #0f56ad;
    --text-light: #f2f2f2;
    --pattern-dark: #0d0d0d;
    --pattern-mid: #2a2a2a;
  }
  * { margin: 0; padding: 0; box-sizing: border-box; }
  html, body {
    width: 1200px;
    height: 801px;
    overflow: hidden;
    background: var(--backdrop);
    font-family: "Montserrat", sans-serif;
  }
  .stage {
    position: relative;
    width: 1200px;
    height: 801px;
  }
  .card {
    position: absolute;
    top: 246px;
    width: 540px;
    height: 309px;
    overflow: hidden;
    box-shadow: 0 6px 18px rgba(0,0,0,0.18);
  }
  .card-front { left: 40px; background: var(--card-white); }
  .card-back {
    left: 620px;
    background: linear-gradient(135deg, var(--pattern-mid) 0%, var(--pattern-dark) 55%, #050505 100%);
  }
  .front-art { position: absolute; inset: 0; }
  .brand-name {
    position: absolute;
    left: 34px;
    top: 112px;
    font-weight: 700;
    font-size: 30px;
    letter-spacing: 2px;
    color: var(--brand-blue);
  }
  .name-tab {
    position: absolute;
    right: 0;
    top: 112px;
    width: 22px;
    height: 22px;
    background: var(--brand-blue);
  }
  .person {
    position: absolute;
    right: 30px;
    top: 110px;
    text-align: right;
  }
  .person-name {
    font-weight: 700;
    font-size: 17px;
    letter-spacing: 0.5px;
    color: var(--brand-blue);
    line-height: 1.2;
  }
  .person-title {
    font-weight: 400;
    font-size: 11.5px;
    color: var(--text-light);
    margin-top: 2px;
  }
  .contact-list {
    position: absolute;
    right: 16px;
    top: 170px;
    list-style: none;
    text-align: right;
  }
  .contact-item {
    display: flex;
    justify-content: flex-end;
    align-items: center;
    gap: 8px;
    font-size: 11.5px;
    color: var(--text-light);
    line-height: 19px;
  }
  .contact-icon { width: 11px; height: 11px; fill: var(--brand-blue); }
  .address {
    position: absolute;
    left: 30px;
    bottom: 14px;
    font-style: normal;
    font-size: 11.5px;
    line-height: 16px;
    color: var(--text-light);
  }
</style>
</head>
<body>
<main class="stage">
  <section class="card card-front" aria-label="Business card front">
    <svg class="front-art" width="540" height="309" viewBox="0 0 540 309" aria-hidden="true">
      <path d="M540,40 C420,44 360,70 335,120 C300,200 260,250 0,252 L0,309 L540,309 Z" fill="var(--card-black)"/>
      <path d="M540,26 C410,30 346,58 320,110 C286,190 246,238 0,238" fill="none" stroke="var(--brand-blue)" stroke-width="6"/>
      <path d="M520,33 C412,40 354,66 328,116 C294,194 254,242 30,244" fill="none" stroke="var(--brand-blue)" stroke-width="1.6"/>
    </svg>
    <div class="brand-name">TA BRAMLEY</div>
    <div class="name-tab"></div>
    <div class="person">
      <div class="person-name">DANIEL PORTER</div>
      <div class="person-title">Managing Director</div>
    </div>
    <ul class="contact-list">
      <li class="contact-item">123 456 789
        <svg class="contact-icon" viewBox="0 0 12 12"><path d="M2.5 1 L4.5 1 L5.3 3.6 L4 4.6 C4.6 6 6 7.4 7.4 8 L8.4 6.7 L11 7.5 L11 9.5 C11 10.4 10.3 11 9.5 11 C5 11 1 7 1 2.5 C1 1.7 1.6 1 2.5 1 Z"/></svg>
      </li>
      <li class="contact-item">info@yourmail.com
        <svg class="contact-icon" viewBox="0 0 12 12"><path d="M1 2.5 H11 V9.5 H1 Z M1.6 3 L6 6.4 L10.4 3" stroke="var(--card-black)" stroke-width="0.8"/></svg>
      </li>
      <li class="contact-item">www.yourwebsite.com
        <svg class="contact-icon" viewBox="0 0 12 12"><circle cx="6" cy="6" r="5"/><path d="M1 6 H11 M6 1 C3.5 3.5 3.5 8.5 6 11 M6 1 C8.5 3.5 8.5 8.5 6 11" fill="none" stroke="var(--card-black)" stroke-width="0.7"/></svg>
      </li>
    </ul>
    <address class="address">Your address, City<br>State, Zip 1234</address>
  </section>

  <section class="card card-back" role="img" aria-label="Embossed repeating brand monogram pattern on black"></section>
</main>
</body>
</html>
```